A4 Single Page Brochure for Private Cloud Offerings

Theme: Futuristic Tech Company

Meridane Systems is looking to offer private cloud services for our enterprise customers in Perth-based data-centres that provides our clients with a lower-cost alternative to Kelvara or QNL yielding better performance.

We are looking for a single A4 brochure with a great graphics design theme to promote these services.

We will be providing five tiers:
- Starter
- Growth
- Professional
- Premier
- Elite

Each plan must list on the brochure the Max VMs, CPU cores, Memory and SSD storage allocated. Refer to the uploaded PNG file.

The brochure must list the following selling points:

- Hosted in a local Perth-based TIER3 and TIER4 datacentres
- WA owned hosting - support local
- Low latency - ultra fast local hosting
- Includes Orvix Host Datacentre licensing
- Includes BrakWall Managed Firewalls for Enterprise level threat detection
- Includes all infrastructure maintenance services
- Full self management of VMs through customer portal
- Includes a 1gbps Internet link
- Predictable fixed monthly fee with no dynamic billing
- No additional charges for Storage Transactions, Internet Usage, VM Snapshots, Datacentre Bandwidth Usage and Firewall Traffic Usage.
- Highly available cluster, no single point of failure.
- Pricing is based on 36 months commit
- Yearly rate increases capped to a maximum of Australian CPI
- All plans have 24/7/365 support with dedicated after hours number.
- Managed backup and managed disaster recovery services can be added to plans

Service provided in accordance with our terms and conditions.

We need the ability to EDIT the brochure to adjust pricing after we receive the final project.

I have uploaded more details on these plans under the attachment PrivateCloudPlans.png.

Please do not utilise "Pushing the Boundaries of Technology" - our brand is being replaced with "Specialised Consulting". New website is under development but not launched yet.

Target Market(s)

Information Technology Sector

Colors
0054AA
0677BA
7BADD7
CADEEF
E8F1F8

Requirements
Must have
• Theme of Meridane is Blue
Should not have
• Extremely stock imagary that just looks "cheap and stock"

```html
<!DOCTYPE html>
<html lang="en">
<head>
<meta charset="utf-8">
<title>Meridane Systems – Private Cloud Brochure</title>
<link href="https://fonts.googleapis.com/css2?family=Montserrat:wght@400;500;600;700;800&display=swap" rel="stylesheet">
<style>
  :root{
    --backdrop:#141a6e;
    --ink:#2e3180;
    --ink-soft:#3b3f8f;
    --paper:#eef2f7;
    --paper-edge:#cadeef;
    --mint:#6fe8c2;
    --navy-pill:#3b3f8f;
    --deep:#17235e;
    --deep-2:#0054aa;
    --sky:#7badd7;
    --white:#ffffff;
  }
  *{box-sizing:border-box;margin:0;padding:0}
  html,body{width:1200px;height:1119px;overflow:hidden}
  body{background:var(--backdrop);font-family:"Montserrat",sans-serif;position:relative}

  .brochure{position:absolute;left:220px;top:20px;width:760px;height:1079px;background:var(--paper);overflow:hidden;box-shadow:0 10px 40px rgba(0,0,0,.45)}

  .top-backdrop{position:absolute;left:0;top:0;width:760px;height:540px;
    background:radial-gradient(ellipse at 60% 20%, #ffffff 0%, #e8f1f8 45%, #cadeef 100%)}
  .edge-band{position:absolute;left:0;top:0;width:22px;height:540px;background:linear-gradient(180deg,#0054aa,#0677ba 60%,#7badd7)}

  .brand{position:absolute;left:440px;top:56px;display:flex;align-items:center;gap:12px}
  .brand-mark{width:34px;height:34px;background:var(--ink)}
  .brand-name{font-weight:700;font-size:34px;color:var(--ink);letter-spacing:1px}
  .tagline{position:absolute;left:406px;top:128px;font-weight:800;font-size:26px;color:var(--ink);white-space:nowrap}

  .intro{position:absolute;left:48px;top:96px;width:350px;color:var(--ink-soft);font-size:14px;line-height:1.42;font-weight:500}
  .intro p+p{margin-top:12px}

  .plans{position:absolute;left:48px;top:310px;width:670px;height:206px;border:1.5px solid var(--ink-soft);background:rgba(255,255,255,.55)}
  .plans table{width:100%;height:100%;border-collapse:collapse;table-layout:fixed;color:var(--ink);font-size:15px}
  .plans col.label-col{width:170px}
  .plans th{font-weight:800;font-size:15px;padding-top:26px;text-align:right;padding-right:12px}
  .plans td{text-align:right;padding-right:12px;font-weight:500;line-height:1.25}
  .plans td.label{text-align:left;padding-left:18px;font-weight:800}
  .plans td.label.soft{font-weight:500}
  .plans .col{border-left:1px solid var(--ink-soft)}
  .plans tr.cost td{font-weight:600;font-size:14px;padding-top:10px;padding-bottom:22px;white-space:nowrap}

  .pill{position:absolute;border-radius:30px;font-weight:700;white-space:nowrap}
  .pill-tiers{left:66px;top:296px;background:var(--navy-pill);color:var(--mint);font-size:14px;padding:5px 16px}
  .pill-larger{left:528px;top:504px;background:var(--navy-pill);color:var(--mint);font-size:14px;padding:5px 16px;font-weight:500}

  .lower{position:absolute;left:0;top:540px;width:760px;height:539px;
    background:linear-gradient(160deg,#1d2b6e 0%,#17235e 40%,#0d3d8a 75%,#0677ba 100%)}
  .lower-art{position:absolute;right:0;top:0;width:420px;height:300px;
    background:radial-gradient(ellipse at 55% 45%, rgba(123,173,215,.55), rgba(23,35,94,0) 70%)}

  .pill-hosted{left:40px;top:562px;background:var(--mint);color:var(--deep);font-size:16px;font-weight:800;padding:9px 22px}

  .points{position:absolute;left:40px;top:614px;width:690px;list-style:none;color:var(--white);font-size:13.5px;line-height:25px;font-weight:500;padding-left:30px}
  .points::before{content:"";position:absolute;left:8px;top:8px;bottom:8px;border-left:1.5px dashed var(--sky)}
  .points li{position:relative}
  .points li::before{content:"";position:absolute;left:-27px;top:9px;width:7px;height:7px;border-radius:50%;background:var(--sky)}
  .points li.cont::before{display:none}

  .pill-terms{left:200px;top:1028px;background:var(--mint);color:var(--deep);font-size:14px;font-weight:600;padding:6px 22px}
</style>
</head>
<body>
<main class="brochure">
  <div class="top-backdrop" role="img" aria-label="Soft light-blue network line pattern"></div>
  <div class="edge-band" role="img" aria-label="Blue circuit-board edge decoration"></div>

  <div class="brand"><span class="brand-mark"></span><span class="brand-name">MERIDANE</span></div>
  <div class="tagline">“Specialised Consulting”</div>

  <section class="intro">
    <p>Meridane Systems is looking to offer private cloud services for our enterprise customers in Perth-based data-centres that provides our clients with a lower-cost alternative to Kelvara or QNL yielding better performance.</p>
    <p>We are looking for a single A4 brochure with a great graphics design theme to promote these services.</p>
  </section>

  <section class="plans">
    <table>
      <colgroup><col class="label-col"><col><col><col><col><col></colgroup>
      <tr><th></th><th class="col">Starter</th><th class="col">Growth</th><th class="col">Professional</th><th class="col">Premier</th><th class="col">Elite</th></tr>
      <tr><td class="label">Max VMs</td><td class="col">5</td><td class="col">10</td><td class="col">15</td><td class="col">20</td><td class="col">25</td></tr>
      <tr><td class="label">CPU cores</td><td class="col">8</td><td class="col">16</td><td class="col">32</td><td class="col">48</td><td class="col">64</td></tr>
      <tr><td class="label">Memory (GB)</td><td class="col">64</td><td class="col">128</td><td class="col">192</td><td class="col">256</td><td class="col">320</td></tr>
      <tr><td class="label">SSD storage (TB)</td><td class="col">3</td><td class="col">8</td><td class="col">15</td><td class="col">20</td><td class="col">30</td></tr>
      <tr class="cost"><td class="label soft">Monthly <b>Cost</b></td><td class="col">$ 1,028.01</td><td class="col">$ 3,426.64</td><td class="col">$ 4,626.05</td><td class="col">$ 5,482.72</td><td class="col">$ 7,196.07</td></tr>
    </table>
  </section>
  <div class="pill pill-tiers">We will be providing five tiers:</div>

  <section class="lower">
    <div class="lower-art" role="img" aria-label="Photo of a digital cloud over a data centre with an engineer at work"></div>
  </section>
  <div class="pill pill-larger">For larger plans, ask us.</div>

  <div class="pill pill-hosted">HOSTED IN A LOCAL PERTH-BASED TIER3 AND TIER4 DATA CENTRES</div>

  <ul class="points">
    <li>- WA owned hosting - support local</li>
    <li>- Low latency - ultra fast local hosting</li>
    <li>- Includes Orvix Host Datacentre licensing</li>
    <li>- Includes BrakWall Managed Firewalls for Enterprise level threat detection</li>
    <li>- Includes all infrastructure maintenance services</li>
    <li>- Full self management of VMs through customer portal</li>
    <li>- Includes a 1gbps Internet link</li>
    <li>- Predictable fixed monthly fee with no dynamic billing</li>
    <li>- No additional charges for Storage Transactions, Internet Usage,</li>
    <li class="cont">&nbsp;&nbsp;VM Snapshots, Datacentre Bandwidth Usage and Firewall Traffic Usage.</li>
    <li>- Highly available cluster, no single point of failure.</li>
    <li>- Pricing is based on 36 months commit</li>
    <li>- Yearly rate increases capped to a maximum of Australian CPI</li>
    <li>- All plans have 24/7/365 support with dedicated after hours number.</li>
    <li>- Managed backup and managed disaster recovery services can be added to plans</li>
  </ul>

  <div class="pill pill-terms">Service provided in accordance with our terms and conditions.</div>
</main>
</body>
</html>
```